Poetry Book Cover Design Project

Looking for a minimalistic book cover design for a collection of poems. The book title is "Before The Lanterns Drift Away Slowly". There are three parts to the book. First covers poetry in the theme of Rage. Second love and desire. The third is strange poems. Essentially the sections are "Rage", "Desire" and the "Strange". The reason for the title "Before The Lanterns Drift Away Slowly" is as if someone is writing these till life changes towards the intended outcome as felt in each poem. I want to have the author's name "Ruvinath Kolongaswe" at the bottom. Ilustration attached.
- Minimalistic

```html
<!DOCTYPE html>
<html lang="en">
<head>
<meta charset="utf-8">
<title>Before The Lanterns Drift Away Slowly — Ruvinath Kolongaswe</title>
<link rel="stylesheet" href="https://fonts.googleapis.com/css2?family=EB+Garamond:wght@400;500&display=swap">
<style>
  :root {
    --paper: #ffffff;
    --title-red: #d9142b;
    --author-ink: #222222;
    --line-blue-deep: #2c3f9a;
    --line-blue-light: #2a9ad6;
  }
  html, body {
    margin: 0;
    padding: 0;
    overflow: hidden;
    background: var(--paper);
  }
  .cover {
    position: relative;
    width: 801px;
    height: 1200px;
    background: var(--paper);
    overflow: hidden;
  }
  .cover__illustration {
    position: absolute;
    left: 0;
    top: 28px;
    width: 470px;
    height: 750px;
  }
  .cover__title {
    position: absolute;
    right: 40px;
    top: 178px;
    margin: 0;
    font-family: "EB Garamond", "Garamond", serif;
    font-weight: 400;
    font-size: 132px;
    line-height: 143px;
    letter-spacing: -0.02em;
    color: var(--title-red);
    text-align: right;
  }
  .cover__title-line {
    display: block;
  }
  .cover__author {
    position: absolute;
    left: 0;
    right: 0;
    top: 1080px;
    margin: 0;
    font-family: "EB Garamond", "Garamond", serif;
    font-weight: 400;
    font-size: 38px;
    letter-spacing: 0.13em;
    color: var(--author-ink);
    text-align: center;
  }
</style>
</head>
<body>
  <main class="cover">
    <svg class="cover__illustration" role="img" aria-label="Single-line blue drawing of several overlapping faces" viewBox="0 0 470 750">
      <defs>
        <linearGradient id="illustrationTone" x1="0" y1="0" x2="0.3" y2="1">
          <stop offset="0" stop-color="#2c3f9a" stop-opacity="0.16"/>
          <stop offset="1" stop-color="#2a9ad6" stop-opacity="0.18"/>
        </linearGradient>
      </defs>
      <path d="M0 0 H430 V445 H315 V750 H0 Z" fill="url(#illustrationTone)"/>
    </svg>

    <h1 class="cover__title">
      <span class="cover__title-line">Before</span>
      <span class="cover__title-line">The</span>
      <span class="cover__title-line">Lanterns</span>
      <span class="cover__title-line">Drift</span>
      <span class="cover__title-line">Away</span>
      <span class="cover__title-line">Slowly</span>
    </h1>

    <p class="cover__author">Ruvinath Kolongaswe</p>
  </main>
</body>
</html>
```